Reel-Horizons

I want a website template for drive-in movie theaters. Here is a website that I would like to be revamped: https://torumek.com/ and https://www.pebblecrestdrivein.com/.

Target Market(s)

Drive-In Movie Theaters

Industry/Entity Type

Drive-In Moviews

Number of Pages Required

5+ page

Font styles to use
Sans Serif

Colors
0054AA
0677BA
7BADD7
CADEEF
E8F1F8

Requirements
Must have
• Movies shown, time movie is to be seen, link to buy tickets, link to join news letter / rewards, chatterloop link, contact page and directions

```html
<!DOCTYPE html>
<html lang="en">
<head>
<meta charset="utf-8">
<title>Moonfield Drive In Theatre</title>
<link rel="stylesheet" href="https://fonts.googleapis.com/css2?family=Great+Vibes&family=Jost:wght@400;500;600&family=Raleway:wght@300;400&display=swap">
<style>
:root{
  --blue:#0054AA;
  --blue-mid:#0677BA;
  --blue-soft:#7BADD7;
  --blue-pale:#CADEEF;
  --blue-mist:#E8F1F8;
  --black:#000;
  --ink:#222;
  --white:#fff;
  --line:#bbb;
}
*{box-sizing:border-box;margin:0;padding:0}
html,body{width:1200px;height:3006px;overflow:hidden}
body{position:relative;background:var(--white);font-family:"Jost",sans-serif;color:var(--ink)}
.abs{position:absolute}
.topbar{left:0;top:0;width:1200px;height:34px;background:var(--blue);color:var(--white);font-size:14px;font-weight:500}
.topbar .covid{left:135px;top:8px}
.topbar .login{right:84px;top:8px;display:flex;align-items:center;gap:4px}
.nav{left:0;top:34px;width:1200px;height:89px;background:var(--black)}
.brand{display:flex;align-items:center;gap:8px;color:var(--white);font-family:"Jost",sans-serif;font-weight:600;font-size:20px}
.brand .dot{width:14px;height:14px;border-radius:50%;background:var(--blue-mid)}
.nav .brand{left:138px;top:30px}
.menu{display:flex;color:var(--white);font-size:12.5px;font-weight:600;letter-spacing:.2px}
.nav .menu{left:321px;top:37px;gap:37px}
.hero{left:0;top:123px;width:1200px;height:596px;background:radial-gradient(ellipse at 50% 20%,#1f4d9a 0%,#0d2454 45%,#060c1c 75%),#060c1c}
.hero-seats{left:0;top:430px;width:1200px;height:166px;background:linear-gradient(180deg,rgba(60,40,30,0) 0%,#3a2a1e 60%,#241a12 100%)}
.hero-card{left:214px;top:32px;width:785px;height:388px;background:var(--white);text-align:center}
.hero-card h1{font-family:"Great Vibes",cursive;font-weight:400;color:var(--blue);font-size:62px;margin-top:60px;line-height:1}
.hero-card p{font-size:14.5px;line-height:29.6px;width:630px;margin:20px auto 0;color:var(--ink)}
.btn{display:inline-flex;align-items:center;justify-content:center;border-radius:26px;font-weight:600;font-size:14.5px}
.btn-solid{background:var(--blue);color:var(--white)}
.btn-line{border:2px solid var(--blue);color:var(--blue);background:var(--white)}
.hero-card .btn{width:171px;height:51px;margin-top:16px}
.section-title{font-family:"Raleway",sans-serif;font-weight:400;font-size:33px;text-align:center;width:1200px;left:0}
.rule{width:44px;height:3px;background:var(--blue);left:578px}
.tabs{left:428px;top:872px;width:343px;height:49px;border:2px solid var(--blue);display:flex;font-family:"Raleway",sans-serif;font-size:17px}
.tabs span{flex:1;display:flex;align-items:center;justify-content:center;color:var(--blue)}
.tabs .on{background:var(--blue);color:var(--white)}
.movie{top:959px;width:224px;text-align:center}
.poster{width:224px;height:258px;position:relative;overflow:hidden}
.price-tag{position:absolute;left:0;top:0;width:0;height:0;border-top:56px solid var(--blue);border-right:110px solid transparent}
.price-tag b{position:absolute;left:9px;top:-48px;color:var(--white);font-weight:500;font-size:16px;white-space:nowrap}
.movie h3{font-weight:500;font-size:17px;margin-top:14px;letter-spacing:.2px}
.movie .time{color:var(--blue);font-weight:500;font-size:16px;margin-top:2px}
.movie .btn{width:170px;height:51px;margin-top:9px;font-size:14.5px}
.dots{left:536px;top:1377px;display:flex;gap:4.5px}
.dots i{width:10px;height:10px;border-radius:50%;background:#ccc}
.dots i.on{background:var(--blue)}
.prices{left:0;top:1460px;width:1200px;height:426px;background:linear-gradient(120deg,#0a5cb3 0%,var(--blue) 50%,#0b58ab 100%)}
.price-card{top:153px;width:280px;height:192px;background:var(--white);border-radius:6px;text-align:center;color:var(--blue)}
.price-card .amt{font-family:"Great Vibes",cursive;font-size:54px;margin-top:48px;line-height:1}
.price-card .age{font-family:"Raleway",sans-serif;font-size:25px;margin-top:12px}
.h2{font-family:"Raleway",sans-serif;font-weight:400;font-size:35px;top:1955px}
.contact-item{left:173px;display:flex;gap:16px}
.icon{width:52px;height:52px;border-radius:50%;background:var(--blue);display:flex;align-items:center;justify-content:center;flex-shrink:0}
.contact-item h4{font-family:"Raleway",sans-serif;font-weight:400;color:var(--blue);font-size:19px;margin-top:-5px}
.contact-item p{font-size:14.5px;line-height:28px;margin-top:2px;font-weight:500}
.field{left:627px;width:351px;border:1px solid var(--line);border-radius:5px;font-size:12.5px;color:#777;padding:0 12px;display:flex;align-items:center}
.submit{left:627px;top:2362px;width:351px;height:43px;border-radius:22px;background:var(--blue);color:var(--white);font-weight:600;font-size:16px;display:flex;align-items:center;justify-content:center;box-shadow:0 6px 12px rgba(0,0,0,.2)}
.footer{left:0;top:2600px;width:1200px;height:406px;background:var(--black);color:var(--white)}
.mailing{left:132px;top:2507px;width:935px;height:160px;background:var(--blue);border-radius:6px;text-align:center;color:var(--white)}
.mailing h2{font-family:"Raleway",sans-serif;font-weight:400;font-size:33px;margin-top:20px}
.mail-input{left:168px;top:79px;width:599px;height:50px;border-radius:25px;background:var(--white);border:2px solid var(--white);display:flex;justify-content:space-between;align-items:center;padding-left:18px;font-size:14px;color:#888}
.mail-input span.btn{height:46px;width:147px;font-size:16px}
.footer .brand{left:520px;top:140px}
.footer .menu{left:201px;top:215px;gap:37px}
.social{left:584px;top:256px;width:31px;height:31px;border-radius:50%;background:var(--white);display:flex;align-items:center;justify-content:center}
.copy{left:0;width:1200px;top:322px;text-align:center;font-size:12.5px;font-weight:500}
</style>
</head>
<body>

<div class="abs topbar">
  <span class="abs covid">Moonfield Covid19 Information Link</span>
  <span class="abs login"><svg width="12" height="13" viewBox="0 0 12 13"><circle cx="6" cy="3.5" r="3" fill="#fff"/><path d="M0 13c0-4 2.5-6 6-6s6 2 6 6z" fill="#fff"/></svg>Login/Sign Up</span>
</div>

<header class="abs nav">
  <div class="abs brand"><span class="dot"></span>Moonfield</div>
  <nav class="abs menu"><span>HOME</span><span>NOW PLAYING</span><span>COMING SOON</span><span>ADMINISTRATION</span><span>DIRECTIONS</span><span>HISTORY</span><span>MERCHANDISE</span><span>FAQS</span></nav>
</header>

<section class="abs hero">
  <div class="abs hero-seats" role="img" aria-label="Audience seated facing a glowing cinema screen"></div>
  <div class="abs hero-card">
    <h1>Moonfield Drive In Theatre</h1>
    <p>Welcome to the Moonfield Drive-In Theatre. We’ve been in Pine Hollow, Florida for more than 70 years. In fact, we are one of the last drive-in theatres in Florida, but we are here to stay! We have one screen often showing first-run movies – with double features five nights a week (closed Monday and Tuesday). Listen to the movie through your FM car radio. (93.1)</p>
    <span class="btn btn-solid">BUY TICKETS NOW</span>
  </div>
</section>

<h2 class="abs section-title" style="top:790px">MOVIES</h2>
<div class="abs rule" style="top:839px"></div>
<div class="abs tabs"><span class="on">NOW SHOWING</span><span>COMING SOON</span></div>

<article class="abs movie" style="left:132px">
  <div class="poster" role="img" aria-label="Vintage hot dog advertisement poster" style="background:linear-gradient(160deg,#e8dcc0,#c9a979 60%,#7a6a4a)"><span class="price-tag"><b>$ 1.00</b></span></div>
  <h3>COPPERLINE HOT DOGS</h3><div class="time">EVERY NIGHT</div><span class="btn btn-line">BUY TICKETS NOW</span>
</article>
<article class="abs movie" style="left:369px">
  <div class="poster" role="img" aria-label="Dark horror film poster" style="background:radial-gradient(circle at 55% 45%,#b5702e,#5a2a10 55%,#1a0a04)"><span class="price-tag"><b>$ 1.00</b></span></div>
  <h3>NIGHT HOLLOW</h3><div class="time">7:45</div><span class="btn btn-line">BUY TICKETS NOW</span>
</article>
<article class="abs movie" style="left:606px">
  <div class="poster" role="img" aria-label="Retro cartoon snack advertisement" style="background:linear-gradient(160deg,#6aa888,#e6a27c 60%,#d46a4e)"><span class="price-tag"><b>$ 1.00</b></span></div>
  <h3>COPPERLINE HOT DOGS</h3><div class="time">EVERY NIGHT</div><span class="btn btn-line">BUY TICKETS NOW</span>
</article>
<article class="abs movie" style="left:843px">
  <div class="poster" role="img" aria-label="Action film poster in black and red" style="background:radial-gradient(circle at 45% 40%,#6a1a22,#2a1216 55%,#c8c8cc)"><span class="price-tag"><b>$ 1.00</b></span></div>
  <h3>CRIMSON COIL</h3><div class="time">9:35</div><span class="btn btn-line">BUY TICKETS NOW</span>
</article>

<div class="abs dots"><i class="on"></i><i></i><i></i><i></i><i></i><i></i><i></i><i></i><i></i></div>

<section class="abs prices">
  <h2 class="abs section-title" style="top:74px;color:var(--white)">TICKET PRICES</h2>
  <div class="abs rule" style="top:120px;background:var(--white)"></div>
  <div class="abs price-card" style="left:152px"><div class="amt">$7</div><div class="age">AGES 10+</div></div>
  <div class="abs price-card" style="left:460px"><div class="amt">$3</div><div class="age">AGES 4-9</div></div>
  <div class="abs price-card" style="left:768px"><div class="amt">Free</div><div class="age">UNDER 4 YEARS</div></div>
</section>

<h2 class="abs h2" style="left:157px">CONTACT US</h2>
<h2 class="abs h2" style="left:614px">GET IN TOUCH</h2>

<div class="abs contact-item" style="top:2049px">
  <span class="icon"><svg width="14" height="18" viewBox="0 0 14 18"><path d="M7 0a7 7 0 0 0-7 7c0 5 7 11 7 11s7-6 7-11a7 7 0 0 0-7-7zm0 9.5A2.5 2.5 0 1 1 7 4.5a2.5 2.5 0 0 1 0 5z" fill="#fff"/></svg></span>
  <div><h4>LOCATION</h4><p>Moonfield Drive-In ~ 4820 Orchard Way<br>N. ~ Fernhill, MN 55099</p></div>
</div>
<div class="abs contact-item" style="top:2170px">
  <span class="icon"><svg width="18" height="14" viewBox="0 0 18 14"><rect width="18" height="14" rx="2" fill="#fff"/><path d="M1 2l8 6 8-6" stroke="#0054AA" stroke-width="1.6" fill="none"/></svg></span>
  <div><h4>EMAIL ADDRESS</h4><p>hello@moonfielddrivein.com</p></div>
</div>
<div class="abs contact-item" style="top:2266px">
  <span class="icon"><svg width="16" height="16" viewBox="0 0 24 24"><path d="M6.6 10.8a15 15 0 0 0 6.6 6.6l2.2-2.2c.3-.3.7-.4 1-.2 1.1.4 2.3.6 3.6.6.6 0 1 .4 1 1V20c0 .6-.4 1-1 1A17 17 0 0 1 3 4c0-.6.4-1 1-1h3.5c.6 0 1 .4 1 1 0 1.3.2 2.5.6 3.6.1.3 0 .7-.2 1z" fill="#fff"/></svg></span>
  <div><h4>PHONE NUMBER</h4><p>(555) 014-2277</p></div>
</div>

<div class="abs field" style="top:2022px;height:48px">Full Name</div>
<div class="abs field" style="top:2087px;height:48px">Email address</div>
<div class="abs field" style="top:2151px;height:48px">Phone Number</div>
<div class="abs field" style="top:2215px;height:119px;align-items:flex-start;padding-top:16px">Message</div>
<div class="abs submit">SUBMIT</div>

<footer class="abs footer">
  <div class="abs brand"><span class="dot"></span>Moonfield</div>
  <nav class="abs menu"><span>HOME</span><span>NOW PLAYING</span><span>COMING SOON</span><span>ADMINISTRATION</span><span>DIRECTIONS</span><span>HISTORY</span><span>MERCHANDISE</span><span>FAQS</span></nav>
  <span class="abs social" aria-label="chatterloop"><svg width="13" height="13" viewBox="0 0 13 13"><circle cx="6.5" cy="6.5" r="4.5" fill="none" stroke="#0054AA" stroke-width="2"/></svg></span>
  <div class="abs copy">© Copyright 2021 &nbsp;company Name &nbsp;&nbsp;&nbsp; | &nbsp;&nbsp;&nbsp; All Rights Reserved</div>
</footer>

<section class="abs mailing">
  <h2>JOIN OUR MAILING LIST</h2>
  <div class="abs mail-input"><span>Enter Email Here</span><span class="btn btn-solid">SUBSCRIBE</span></div>
</section>

</body>
</html>
```